Vigil Ledger Suite (Web Design)

Design with your logo. Background in black or dark. Elegant style, it's a website for professional people only. Our company provides a cloud software manager for Funeral Services Companies.

Target Market(s)

Professional of Funeral Services.

Coding

Coded - Design and coding required

Number of Pages Required

3 page

Font styles to use
Sans Serif

Colors
fbee3d
000000
5c5c5c

Requirements
Must have
• Design of the website should be similar to our logo colors.

```html
<!DOCTYPE html>
<html lang="en">
<head>
<meta charset="utf-8">
<title>Vigil Ledger Suite</title>
<link href="https://fonts.googleapis.com/css2?family=Montserrat:wght@400;500;600&display=swap" rel="stylesheet">
<style>
:root{
  --yellow:#fbee3d;
  --gold:#f5cf14;
  --black:#000000;
  --ink:#1f1f1f;
  --grey:#5c5c5c;
  --panel:#4a4a4a;
  --light:#e8e8e8;
  --card:#e6e6e6;
  --footer:#1b1b1b;
  --footer-text:#b5b5b5;
  --white:#ffffff;
}
*{box-sizing:border-box;margin:0;padding:0}
html,body{width:1200px;height:2635px;overflow:hidden}
body{font-family:"Montserrat",Arial,sans-serif;color:var(--ink);background:var(--white)}
.btn{display:inline-block;background:var(--gold);color:var(--ink);font-size:13px;font-weight:500;padding:8px 12px;border-radius:3px;text-decoration:none}

.hero{position:relative;height:615px;background:linear-gradient(120deg,#2e2c28 0%,#4a4540 45%,#2b2926 75%,#1e1d1b 100%);color:var(--white)}
.hero-scene{position:absolute;inset:0}
.hero-shade{position:absolute;inset:0;background:rgba(0,0,0,.3)}
.brand{position:absolute;left:144px;top:32px;display:flex;align-items:center;gap:10px;font-size:22px;font-weight:600;color:var(--gold)}
.brand-dot{width:22px;height:22px;border-radius:50%;background:var(--gold)}
.nav{position:absolute;right:144px;top:13px;display:flex;gap:34px;font-size:14px}
.nav a{color:var(--white);text-decoration:none}
.nav a.active{color:var(--gold)}
.hero-copy{position:absolute;left:144px;top:240px}
.hero-copy h1{font-size:32px;font-weight:400;line-height:41px;margin-bottom:12px}
.dots{position:absolute;left:556px;top:576px;display:flex;gap:12px}
.dots span{width:12px;height:12px;border-radius:50%;background:#c9c9c9}
.dots span.on{background:var(--gold)}

.intro{height:253px;text-align:center;padding-top:72px}
h2.section-title{font-size:33px;font-weight:400;color:var(--ink)}
.intro p{width:910px;margin:14px auto 0;font-size:13px;line-height:22px;color:#444}

.features{height:337px;background:var(--light);display:flex;justify-content:center;gap:0;padding-top:80px}
.feature{width:237px;text-align:center}
.feature-icon{width:97px;height:97px;border-radius:50%;background:var(--gold);margin:0 auto;display:flex;align-items:center;justify-content:center}
.feature h3{font-size:17px;font-weight:400;margin:15px 0 6px}
.feature p{font-size:11px;line-height:16px;color:#444;width:195px;margin:0 auto}

.news{position:relative;height:401px;text-align:center;padding-top:70px}
.news-card{position:absolute;left:144px;top:129px;width:910px;height:191px;background:var(--card);display:flex;text-align:left}
.news-photo{width:320px;height:191px;background:linear-gradient(135deg,#c9d2d9,#7f8a93 50%,#4d4a47)}
.news-body{padding:30px 30px 0 30px}
.news-body h3{font-size:17px;font-weight:500}
.news-date{font-size:12px;margin:10px 0 18px}
.news-body p{font-size:11px;line-height:20px;color:#444}
.news-more{font-size:10px;font-weight:600;text-decoration:underline;color:var(--ink);display:inline-block;margin-top:4px}
.arrow{position:absolute;top:210px}

.spotlight{height:399px;display:flex}
.spotlight-copy{width:600px;background:var(--panel);padding:58px 60px 0 144px;color:#ddd}
.spotlight-copy h2{font-size:32px;font-weight:400;color:var(--gold);margin-bottom:14px}
.spotlight-copy p{font-size:11px;line-height:19px;margin-bottom:14px}
.spotlight-photo{width:600px;background:linear-gradient(110deg,#cfd5da,#8d99a4 45%,#e7e4df 80%,#b9aea2)}

.contact{height:309px;text-align:center;padding-top:75px}
.contact p{width:910px;margin:12px auto 16px;font-size:13px;line-height:21px;color:#444}

.footer{height:321px;background:var(--footer);color:var(--footer-text);position:relative;padding:0 144px}
.footer-cols{display:flex;padding-top:50px}
.footer h4{color:var(--white);font-size:18px;font-weight:400;margin-bottom:12px}
.col-blog{width:323px}
.col-tags{width:306px}
.col-news{width:287px}
.post{display:flex;gap:11px;margin-bottom:16px}
.post-thumb{width:67px;height:44px;flex:none;background:linear-gradient(135deg,#1d4f77,#5b8fb0)}
.post-thumb.alt{background:linear-gradient(135deg,#6a6259,#b8b0a4)}
.post p{font-size:10.5px;line-height:16px}
.tags{display:flex;flex-wrap:wrap;gap:9px 9px;width:270px}
.tag{background:#444;color:#ccc;font-size:12px;padding:5px 10px}
.footer-rule{position:absolute;left:144px;right:144px;top:237px;border-top:1px solid #444}
.footer-links{position:absolute;left:144px;top:264px;font-size:11px;color:#ccc}
.copyright{position:absolute;left:144px;top:292px;font-size:11px}
.social{position:absolute;right:144px;top:262px;display:flex;gap:16px}
.social span{width:18px;height:18px;border-radius:50%;background:#8a8a8a}
</style>
</head>
<body>

<header class="hero">
  <div class="hero-scene" role="img" aria-label="Professional working on a laptop and tablet at a desk"></div>
  <div class="hero-shade"></div>
  <div class="brand"><span class="brand-dot"></span>Vigil Ledger Suite</div>
  <nav class="nav">
    <a class="active" href="#">Home</a><a href="#">Solutions</a><a href="#">Features</a><a href="#">Reviews</a><a href="#">Blog</a><a href="#">Contact</a>
  </nav>
  <div class="hero-copy">
    <h1>Maecenas tortor<br>accumsan quam varius</h1>
    <a class="btn" href="#">Read More</a>
  </div>
  <div class="dots"><span class="on"></span><span></span><span></span><span></span></div>
</header>

<section class="intro">
  <h2 class="section-title">Etiam mattis augue vehicula</h2>
  <p>Pellentesque blandit lacus eget nunc faucibus, et tincidunt eros viverra. Phasellus consequat sagittis nisi suscipit feugiat. Cras eget leo sed nunc hendrerit ultricies eu at nisl. Praesent iaculis faucibus urna sit amet lacinia. Maecenas consequat justo enim, ac mattis massa imperdiet quis. Fusce eget neque elit. Sed augue orci, elementum in magna congue, tincidunt vulputate erat. Aliquam consectetur orci molestie dictum molestie.</p>
</section>

<section class="features">
  <div class="feature">
    <div class="feature-icon"><svg width="56" height="40" viewBox="0 0 56 40"><path d="M14 36h30a9 9 0 0 0 0-18 13 13 0 0 0-25-3A10 10 0 0 0 14 36z" fill="none" stroke="#1f1f1f" stroke-width="2.5"/></svg></div>
    <h3>Aliquam erat</h3>
    <p>Aenean placerat, nibh vel accumsan aliquet, magna nibh accumsan nibh, ac tempus nunc ipsum ac tellus</p>
  </div>
  <div class="feature">
    <div class="feature-icon"><svg width="52" height="52" viewBox="0 0 52 52" fill="none" stroke="#1f1f1f" stroke-width="2.2"><rect x="4" y="8" width="44" height="38" rx="3"/><line x1="4" y1="16" x2="48" y2="16"/><circle cx="15" cy="25" r="4"/><circle cx="26" cy="25" r="4"/><circle cx="37" cy="25" r="4"/><circle cx="15" cy="37" r="4"/><circle cx="26" cy="37" r="4"/><circle cx="37" cy="37" r="4"/></svg></div>
    <h3>Etiam mattis</h3>
    <p>Aenean placerat, nibh vel accumsan aliquet, magna nibh accumsan nibh, ac tempus nunc ipsum ac tellus</p>
  </div>
  <div class="feature">
    <div class="feature-icon"><svg width="54" height="48" viewBox="0 0 54 48" fill="none" stroke="#1f1f1f" stroke-width="2.2"><path d="M4 6h30v20H16l-7 7v-7H4z"/><path d="M20 30v6h18l7 7v-7h5V16H38"/><line x1="10" y1="13" x2="28" y2="13"/><line x1="10" y1="19" x2="24" y2="19"/></svg></div>
    <h3>Curabitur venenatis</h3>
    <p>Aenean placerat, nibh vel accumsan aliquet, magna nibh accumsan nibh, ac tempus nunc ipsum ac tellus</p>
  </div>
  <div class="feature">
    <div class="feature-icon"><svg width="56" height="46" viewBox="0 0 56 46" fill="none" stroke="#1f1f1f" stroke-width="2.2"><circle cx="28" cy="12" r="7"/><path d="M17 40v-8a11 11 0 0 1 22 0v8"/><circle cx="11" cy="20" r="5"/><path d="M3 40v-5a8 8 0 0 1 12-7"/><circle cx="45" cy="20" r="5"/><path d="M53 40v-5a8 8 0 0 0-12-7"/></svg></div>
    <h3>Aenean placerat</h3>
    <p>Aenean placerat, nibh vel accumsan aliquet, magna nibh accumsan nibh, ac tempus nunc ipsum ac tellus</p>
  </div>
</section>

<section class="news">
  <h2 class="section-title">Vestibulum condimentum</h2>
  <svg class="arrow" style="left:54px" width="20" height="28" viewBox="0 0 20 28"><path d="M16 2L4 14l12 12" fill="none" stroke="#777" stroke-width="3"/></svg>
  <article class="news-card">
    <div class="news-photo" role="img" aria-label="Team working at computers in a bright office"></div>
    <div class="news-body">
      <h3>Maecenas vel tortor accumsan quam varius imperdiet</h3>
      <div class="news-date">April, 19 - 2019 &nbsp;at &nbsp;10:15 AM</div>
      <p>Phasellus consequat sagittis nisi suscipit feugiat. Cras eget leo sed nunc hendrerit ultricies eu at nisl. Praesent iaculis faucibus urna sit amet lacinia. Maecenas consequat justo enim, ac mattis massa imperdiet quis. Fusce eget neque elit. Sed augue orci, elementum in magna congue.</p>
      <a class="news-more" href="#">READ MORE</a>
    </div>
  </article>
  <svg class="arrow" style="right:54px" width="20" height="28" viewBox="0 0 20 28"><path d="M4 2l12 12L4 26" fill="none" stroke="#777" stroke-width="3"/></svg>
</section>

<section class="spotlight">
  <div class="spotlight-copy">
    <h2>Cras augue magna</h2>
    <p>Aenean sed quam non sapien faucibus consequat vitae sit amet orci. Praesent quis risus mi. In mollis nulla in pulvinar dictum. Vivamus interdum sagittis felis, ut dapibus ligula feugiat ac. In dictum sapien eu tellus finibus fermentum. Aenean faucibus lacus ut mollis commodo. Donec vestibulum odio sem, ac laoreet massa ullamcorper id. Donec molestie nisi et tellus hendrerit vehicula. Nunc eu ligula sed quam pulvinar maximus in vitae eros. Proin porta fermentum ipsum, vel porttitor turpis venenatis luctus. Vivamus volutpat eu sapien quis tempus. Aenean feugiat viverra lorem ac sagittis. Donec sit amet lectus nec mi tempor laoreet ac nec nunc. Duis id auctor sapien.</p>
    <a class="btn" href="#">Read More</a>
  </div>
  <div class="spotlight-photo" role="img" aria-label="Woman reviewing a spreadsheet on a desktop monitor"></div>
</section>

<section class="contact">
  <h2 class="section-title">Suspendisse elit ligula</h2>
  <p>Pellentesque magna orci, placerat at nisl at, porta ultrices turpis. Fusce in eros non orci posuere viverra ut a lectus. In mattis, lorem sit amet consequat placerat, augue nulla mollis turpis, vitae egestas est tellus in nulla. Vestibulum convallis rutrum tincidunt. Aenean sit amet suscipit leo. Aenean commodo luctus ipsum, at pulvinar ipsum rutrum ut. Phasellus non volutpat eros. Pellentesque pharetra vehicula risus vitae sagittis.</p>
  <a class="btn" href="#">Contact Us</a>
</section>

<footer class="footer">
  <div class="footer-cols">
    <div class="col-blog">
      <h4>Blog</h4>
      <div class="post"><div class="post-thumb" role="img" aria-label="Blog post thumbnail"></div><p>Etiam mattis augue vehicula odio posuere,<br>sit amet tempus lectus luctus. Nulla<br>facilisi. Etiam vel massa.</p></div>
      <div class="post"><div class="post-thumb alt" role="img" aria-label="Blog post thumbnail"></div><p>Quisque aliquet ex nec est vestibulum<br>pulvinar. Pellentesque convallis molestie<br>enim sit amet efficitur.</p></div>
    </div>
    <div class="col-tags">
      <h4>Tags</h4>
      <div class="tags"><span class="tag">Fusce</span><span class="tag">Aenean</span><span class="tag">Proin</span><span class="tag">Curabitur</span><span class="tag">Pellentesque</span><span class="tag">Nulla</span><span class="tag">Vivamus</span><span class="tag">Fusce</span><span class="tag">Vestibulum</span></div>
    </div>
    <div class="col-news">
      <h4>News</h4>
      <div class="post"><div class="post-thumb alt" role="img" aria-label="News thumbnail"></div><p>Etiam mattis augue vehicula odio posuere,<br>sit amet tempus lectus luctus. Nulla<br>facilisi. Etiam vel massa.</p></div>
      <div class="post"><div class="post-thumb" role="img" aria-label="News thumbnail"></div><p>Quisque aliquet ex nec est vestibulum<br>pulvinar. Pellentesque convallis molestie<br>enim sit amet efficitur.</p></div>
    </div>
  </div>
  <div class="footer-rule"></div>
  <div class="footer-links">Home &nbsp;| &nbsp;Solutions &nbsp;| &nbsp;Features &nbsp;| &nbsp;Reviews &nbsp;| &nbsp;Blog &nbsp;| &nbsp;Contact</div>
  <div class="copyright">Copyright © 2019 &nbsp;Vigil Ledger Suite. &nbsp;All rights reserved.</div>
  <div class="social"><span></span><span></span><span></span></div>
</footer>

</body>
</html>
```